Business Card Design

New business card design

Target Market(s)

Residential & Commercial Property Managers

Industry/Entity Type

Plumbing Services

Contact Information for Business Card

Name - Rowan Keddle, title - Director, Phone Number - 0431 286 517, email - rowan@tbk-plumbing.com.au, Company ABN - 73 215 904 386,

Font styles to use
Sans Serif

Colors
0054AA
0677BA
7BADD7
CADEEF
E8F1F8

```html
<!DOCTYPE html>
<html lang="en">
<head>
<meta charset="utf-8">
<title>TBK Plumbing Services – Business Card</title>
<link rel="stylesheet" href="https://fonts.googleapis.com/css2?family=Montserrat:wght@400;500;700&display=swap">
<style>
  :root {
    --bg: #e9edf1;
    --card-dark: #1f262d;
    --card-light: #ffffff;
    --ink: #1f262d;
    --ink-soft: #39434d;
    --accent: #29a8e0;
    --text-light: #ffffff;
    --shadow: 0 14px 34px rgba(20, 28, 36, 0.22);
  }
  * { box-sizing: border-box; margin: 0; padding: 0; }
  html, body {
    width: 1200px; height: 912px; overflow: hidden;
    background: var(--bg);
    font-family: "Montserrat", sans-serif;
  }
  .canvas {
    position: relative; width: 1200px; height: 912px;
    display: flex; flex-direction: column; align-items: center; justify-content: center; gap: 48px;
  }
  .card {
    position: relative; width: 620px; height: 378px;
    border-radius: 18px; overflow: hidden; box-shadow: var(--shadow);
  }
  .card--front {
    background: var(--card-dark);
    display: flex; align-items: center; justify-content: center;
  }
  .card--back { display: flex; background: var(--card-dark); }
  .back__brand {
    width: 50%; background: var(--card-light);
    display: flex; align-items: center; justify-content: center;
  }
  .wordmark { display: flex; align-items: center; gap: 12px; }
  .wordmark__dot { width: 14px; height: 14px; border-radius: 50%; background: var(--accent); flex: none; }
  .wordmark__name {
    font-weight: 500; font-size: 26px; letter-spacing: 0.06em; line-height: 1.15; text-transform: lowercase;
  }
  .wordmark__name span { display: block; font-size: 13px; letter-spacing: 0.42em; }
  .card--front .wordmark__name { color: var(--ink-soft); font-size: 38px; }
  .card--front .wordmark__name span { font-size: 17px; }
  .card--front .wordmark__dot { width: 18px; height: 18px; }
  .back__brand .wordmark__name { color: var(--ink); }

  .back__details {
    width: 50%; padding: 70px 34px 0 44px; color: var(--text-light);
  }
  .person__name { color: var(--accent); font-weight: 700; font-size: 27px; line-height: 1.1; }
  .person__title { font-size: 16px; font-weight: 400; margin-top: 2px; }
  .divider { display: block; width: 12px; height: 2px; background: var(--accent); margin: 16px 0 14px; }
  .abn { font-size: 16px; }
  .abn__label { color: var(--accent); }
  .contact { list-style: none; font-size: 16px; }
  .contact li { display: flex; align-items: center; gap: 9px; margin-bottom: 6px; white-space: nowrap; }
  .contact li.contact__email { font-size: 14px; }
  .contact svg { width: 15px; height: 15px; flex: none; fill: var(--accent); }
</style>
</head>
<body>
  <main class="canvas">
    <section class="card card--front" aria-label="Card front">
      <div class="wordmark">
        <span class="wordmark__dot"></span>
        <p class="wordmark__name">tbk<span>plumbing services</span></p>
      </div>
    </section>

    <section class="card card--back" aria-label="Card back">
      <div class="back__brand">
        <div class="wordmark">
          <span class="wordmark__dot"></span>
          <p class="wordmark__name">tbk<span>plumbing services</span></p>
        </div>
      </div>
      <div class="back__details">
        <h1 class="person__name">Rowan Keddle</h1>
        <p class="person__title">Director</p>
        <span class="divider"></span>
        <p class="abn"><span class="abn__label">ABN</span> - 73 215 904 386</p>
        <span class="divider"></span>
        <ul class="contact">
          <li>
            <svg viewBox="0 0 24 24" aria-hidden="true"><path d="M6.6 10.8a15.1 15.1 0 0 0 6.6 6.6l2.2-2.2a1 1 0 0 1 1-.25 11.4 11.4 0 0 0 3.6.57 1 1 0 0 1 1 1V20a1 1 0 0 1-1 1A17 17 0 0 1 3 4a1 1 0 0 1 1-1h3.5a1 1 0 0 1 1 1c0 1.25.2 2.45.57 3.57a1 1 0 0 1-.25 1z"/></svg>
            0431 286 517
          </li>
          <li class="contact__email">
            <svg viewBox="0 0 24 24" aria-hidden="true"><path d="M2 5h20v14H2z M3.5 6.5 12 13l8.5-6.5" fill="none" stroke="#29a8e0" stroke-width="2"/><path d="M2 5h20L12 12.5z"/></svg>
            rowan@tbk-plumbing.com.au
          </li>
        </ul>
      </div>
    </section>
  </main>
</body>
</html>
```